Product Design for VelaMira

Design Brief for VelaMira Product Packaging

Objective:
Create a cohesive, elegant, and brand-consistent packaging design for the VelaMira product line. The signature visual theme should reflect luxury, femininity, and clean beauty values.

---

🎨 Core Design Direction

Unified Aesthetic: All containers must prominently feature the floral pattern shown in "Pattern Reference: Image 3". This design serves as the brand's signature aesthetic and must be applied uniformly across all SKUs.

Brand Logo Placement: The VelaMira logo (provided) should be clearly visible and harmoniously integrated into the patterned background.

Color Palette: Base colors should complement the brand’s primary palette: black, blush pink, and white.

---

🧴 Product-Specific Packaging Specifications

1. Mascara

Bottle Type: Sleek mascara tube with a wand applicator

Capacity: 5ml

Design: Use floral pattern from Pattern Reference Image 3. Ensure the pattern does not obstruct the readability of the logo or any regulatory text.

2. Eyebrow Growth Serum

Bottle Type: 5ml tube with fine-tip brush applicator

Capacity: 5ml

Design: Same floral pattern, scaled and applied proportionally to match the mascara for consistency

3. Eyelash Growth Serum

Bottle Type: 5ml tube with fine-tip brush (similar to the eyebrow serum, unless otherwise advised)

Capacity: 5ml

Design: Identical styling to maintain unity across lash & brow products

4. Anti-Aging Serum or Lotion

Bottle Type: 30ml airless pump bottle (preferred for hygiene and product stability)

Capacity: 30ml

Design: Apply floral pattern from Pattern Reference and scale appropriately for larger surface area

5. Hair Growth Spray

Bottle Type: 50ml fine mist spray bottle

Capacity: 50ml

Design: Pattern applied and scaled for taller profile; maintain visual harmony with skincare line

---

📦 Additional Notes

Please ensure packaging aligns with clean beauty standards (no overly glossy plastic finishes, avoid excessive secondary packaging unless sustainable).

Materials should be eco-conscious where possible.

If embossing, foil stamping, or UV finishing is available for logo accents, please suggest options.

```html
<!DOCTYPE html>
<html lang="en">
<head>
<meta charset="utf-8">
<title>VelaMira Packaging Labels</title>
<link href="https://fonts.googleapis.com/css2?family=Lato:wght@300;400;700&display=swap" rel="stylesheet">
<style>
  :root {
    --backdrop: #e8e8e9;
    --panel: #0a0a0b;
    --cream: #f4ecdc;
    --coral: #e8906f;
    --pattern-light: #eef3f7;
    --pattern-coral: #e4714f;
    --pattern-blush: #eeb6a6;
  }
  * { margin: 0; padding: 0; box-sizing: border-box; }
  html, body { width: 1200px; height: 887px; overflow: hidden; background: var(--backdrop); }
  body { position: relative; font-family: 'Lato', sans-serif; color: var(--cream); }

  .label { position: absolute; box-shadow: 2px 3px 4px rgba(0,0,0,0.18); }
  .floral-fill {
    position: absolute; inset: 0;
    background: linear-gradient(135deg, var(--pattern-light) 0%, var(--pattern-blush) 30%, var(--pattern-coral) 50%, var(--pattern-blush) 70%, var(--pattern-light) 100%);
  }
  .panel {
    position: absolute; background: var(--panel);
    display: flex; flex-direction: column; align-items: center; text-align: center;
  }
  .brand-name { font-family: 'Lato', sans-serif; font-weight: 400; color: var(--cream); white-space: nowrap; }
  .brand-vertical { transform: rotate(-90deg); display: block; }
  .product-name { font-weight: 700; line-height: 1.15; }
  .tagline { font-weight: 300; line-height: 1.3; }
  .volume { font-weight: 300; line-height: 1.3; }
  .info p { line-height: 1.22; font-weight: 300; }
  .info b { font-weight: 700; display: block; }
  .info .block { margin-bottom: 4px; }
  .badges { display: grid; justify-items: center; }
  .badge { display: flex; flex-direction: column; align-items: center; color: var(--coral); line-height: 1.1; }
  .badge svg { display: block; }
  .distributor { font-weight: 300; line-height: 1.25; }
  .distributor b { font-weight: 700; }

  /* Hair growth spray */
  .label-spray { left: 39px; top: 74px; width: 557px; height: 354px; }
  .label-spray .front { left: 91px; top: 32px; width: 95px; height: 289px; }
  .label-spray .front .brand-slot { height: 190px; width: 95px; display: flex; align-items: center; justify-content: center; }
  .label-spray .brand-name { font-size: 36px; }
  .label-spray .product-name { font-size: 11.5px; margin-top: 4px; }
  .label-spray .tagline { font-size: 8.6px; margin-top: 6px; }
  .label-spray .volume { font-size: 8.6px; margin-top: 12px; }
  .label-spray .back { left: 370px; top: 32px; width: 96px; height: 289px; padding-top: 13px; font-size: 8.4px; }
  .label-spray .badges { grid-template-columns: 1fr 1fr; column-gap: 12px; row-gap: 6px; margin-top: 4px; }
  .label-spray .badge { font-size: 4px; }
  .label-spray .distributor { font-size: 7.8px; margin-top: 10px; }

  /* Face serum */
  .label-serum { left: 615px; top: 194px; width: 557px; height: 234px; }
  .label-serum .front { left: 69px; top: 35px; width: 141px; height: 164px; padding-top: 24px; }
  .label-serum .brand-name { font-size: 25px; }
  .label-serum .product-name { font-size: 11.5px; margin-top: 18px; }
  .label-serum .tagline { font-size: 8.6px; margin-top: 7px; }
  .label-serum .volume { font-size: 8.6px; margin-top: 14px; }
  .label-serum .back { left: 347px; top: 35px; width: 142px; height: 164px; padding-top: 13px; font-size: 7.4px; }
  .label-serum .info .block { margin-bottom: 3px; }
  .label-serum .inline b { display: inline; }
  .label-serum .badges { grid-template-columns: repeat(4, 1fr); column-gap: 8px; margin-top: 6px; }
  .label-serum .badge { font-size: 3.6px; }
  .label-serum .distributor { font-size: 7.6px; margin-top: 9px; }

  /* Small tubes */
  .label-tube { top: 455px; width: 252px; height: 363px; }
  .tube-lash { left: 220px; }
  .tube-mascara { left: 489px; }
  .tube-brow { left: 758px; }
  .label-tube .front { left: 35px; top: 33px; width: 55px; height: 296px; }
  .label-tube .front .brand-slot { height: 190px; width: 55px; display: flex; align-items: center; justify-content: center; }
  .label-tube .brand-name { font-size: 29px; }
  .label-tube .product-name { font-size: 9.4px; margin-top: 7px; }
  .label-tube .tagline { font-size: 7.2px; margin-top: 6px; }
  .label-tube .volume { font-size: 7.6px; margin-top: 10px; }
  .label-tube .back { left: 161px; top: 33px; width: 55px; height: 296px; padding-top: 16px; font-size: 7.6px; justify-content: flex-start; }
  .label-tube .badges { row-gap: 5px; }
  .label-tube .badge { font-size: 3.4px; }
  .label-tube .distributor { font-size: 6.4px; position: absolute; bottom: 15px; left: 0; right: 0; }
</style>
</head>
<body>
<svg width="0" height="0" style="position:absolute">
  <defs>
    <symbol id="icon-paraben" viewBox="0 0 24 24">
      <circle cx="12" cy="12" r="10.5" fill="none" stroke="currentColor" stroke-width="1.2"/>
      <path d="M10 6h4M10.8 6v5l-3.5 6.5h9.4L13.2 11V6" fill="none" stroke="currentColor" stroke-width="1.1"/>
      <path d="M5 5l14 14" stroke="currentColor" stroke-width="1.1"/>
    </symbol>
    <symbol id="icon-tested" viewBox="0 0 24 24">
      <circle cx="12" cy="12" r="10.5" fill="none" stroke="currentColor" stroke-width="1.2"/>
      <path d="M10 11V6.5M14 11V6.5" stroke="currentColor" stroke-width="1.3" stroke-linecap="round"/>
      <circle cx="12" cy="14.5" r="3.5" fill="none" stroke="currentColor" stroke-width="1.1"/>
    </symbol>
    <symbol id="icon-cruelty" viewBox="0 0 24 24">
      <circle cx="12" cy="12" r="10.5" fill="none" stroke="currentColor" stroke-width="1.2"/>
      <path d="M12 5.5c2.5 3.5 4 5.7 4 8a4 4 0 0 1-8 0c0-2.3 1.5-4.5 4-8z" fill="none" stroke="currentColor" stroke-width="1.1"/>
    </symbol>
    <symbol id="icon-roots" viewBox="0 0 24 24">
      <circle cx="12" cy="12" r="10.5" fill="none" stroke="currentColor" stroke-width="1.2"/>
      <path d="M12 5.5c2.5 3.5 4 5.7 4 8a4 4 0 0 1-8 0c0-2.3 1.5-4.5 4-8z" fill="none" stroke="currentColor" stroke-width="1.1"/>
      <path d="M12 18v-7M12 14l-2-2M12 13l2-2" fill="none" stroke="currentColor" stroke-width="0.9"/>
    </symbol>
  </defs>
</svg>

<!-- Hair Growth Spray -->
<section class="label label-spray">
  <div class="floral-fill" role="img" aria-label="Signature floral pattern of coral watercolour blossoms on pale blue"></div>
  <div class="panel front">
    <div class="brand-slot"><span class="brand-name brand-vertical">VelaMira</span></div>
    <p class="product-name">Hair Growth<br>Spray</p>
    <p class="tagline">Stimulates<br>+Strengthens</p>
    <p class="volume">50ml / 1.7 fl.oz.</p>
  </div>
  <div class="panel back info">
    <p class="block"><b>Directions:</b>Spray onto clean scalp. Gently massage. Use daily.</p>
    <p class="block"><b>Ingredients:</b>Aqua, Caffeine, Biotin, Ginseng Extract...</p>
    <p class="block"><b>Caution:</b>Avoid contact with eyes. For external use only.</p>
    <div class="badges">
      <div class="badge"><svg width="22" height="22"><use href="#icon-paraben"/></svg>Paraben<br>Free</div>
      <div class="badge"><svg width="22" height="22"><use href="#icon-tested"/></svg>Dermatologist<br>Tested</div>
      <div class="badge"><svg width="22" height="22"><use href="#icon-cruelty"/></svg>Cruelty<br>Free</div>
      <div class="badge"><svg width="22" height="22"><use href="#icon-roots"/></svg>Strengthens<br>Roots</div>
    </div>
    <p class="distributor">Distributed by<br><b>VelaMira,</b><br>London, UK<br>velamirabeauty.com</p>
  </div>
</section>

<!-- Anti-Aging Face Serum -->
<section class="label label-serum">
  <div class="floral-fill" role="img" aria-label="Signature floral pattern of coral watercolour blossoms on pale blue"></div>
  <div class="panel front">
    <span class="brand-name">VelaMira</span>
    <p class="product-name">Anti-Aging Face<br>Serum</p>
    <p class="tagline">Hydrates • Firms • Brightens</p>
    <p class="volume">30ml / 1.0 fl.oz.</p>
  </div>
  <div class="panel back info">
    <p class="block"><b>Directions:</b>Apply 1–2 pumps to clean, dry skin. Use AM &amp; PM.</p>
    <p class="block"><b>Directions:</b>Aqua, Hyaluronic Acid, Niacinamide, Retinol...</p>
    <p class="block inline"><b>Caution:</b>&nbsp; For external use only.</p>
    <div class="badges">
      <div class="badge"><svg width="20" height="20"><use href="#icon-paraben"/></svg>Paraben<br>Free</div>
      <div class="badge"><svg width="20" height="20"><use href="#icon-tested"/></svg>Dermatologist<br>Tested</div>
      <div class="badge"><svg width="20" height="20"><use href="#icon-cruelty"/></svg>Cruelty<br>Free</div>
      <div class="badge"><svg width="20" height="20"><use href="#icon-roots"/></svg>Strengthens<br>Roots</div>
    </div>
    <p class="distributor">Distributed by: <b>VelaMira</b>,<br>London, UK</p>
  </div>
</section>

<!-- Eyelash Growth Serum -->
<section class="label label-tube tube-lash">
  <div class="floral-fill" role="img" aria-label="Signature floral pattern of coral watercolour blossoms on pale blue"></div>
  <div class="panel front">
    <div class="brand-slot"><span class="brand-name brand-vertical">VelaMira</span></div>
    <p class="product-name">Eyelash<br>Growth<br>Serum</p>
    <p class="tagline">Longer +<br>Fuller Lashes</p>
    <p class="volume">5ml/<br>0.17 fl.oz.</p>
  </div>
  <div class="panel back info">
    <p class="block"><b>Ingredients:</b>Aqua, Myristoyl Pentapeptide -17</p>
    <p class="block"><b>Caution:</b>Avoid direct contact with eyes. For external use only.</p>
    <div class="badges" style="margin-top:12px">
      <div class="badge"><svg width="19" height="19"><use href="#icon-paraben"/></svg>Paraben Free</div>
      <div class="badge"><svg width="19" height="19"><use href="#icon-tested"/></svg>Dermatologist Tested</div>
      <div class="badge"><svg width="19" height="19"><use href="#icon-roots"/></svg>Strengthens Roots</div>
      <div class="badge"><svg width="19" height="19"><use href="#icon-cruelty"/></svg>Cruelty Free</div>
    </div>
    <p class="distributor">Distributed by<br><b>VelaMira</b>,<br>London, UK</p>
  </div>
</section>

<!-- Volumizing Mascara -->
<section class="label label-tube tube-mascara">
  <div class="floral-fill" role="img" aria-label="Signature floral pattern of coral watercolour blossoms on pale blue"></div>
  <div class="panel front">
    <div class="brand-slot"><span class="brand-name brand-vertical">VelaMira</span></div>
    <p class="product-name" style="margin-top:16px">Volumizing<br>Mascara</p>
    <p class="tagline">Lengthening<br>&amp;<br>Defining</p>
    <p class="volume">5ml/<br>0.17 fl.oz.</p>
  </div>
  <div class="panel back info">
    <p class="block"><b>Ingredients:</b>Aqua, Glyceryl Stearate, CI 77499...</p>
    <p class="block"><b>Caution:</b>Avoid direct contact with eyes.</p>
    <div class="badges" style="margin-top:14px">
      <div class="badge"><svg width="19" height="19"><use href="#icon-paraben"/></svg>Paraben Free</div>
      <div class="badge"><svg width="19" height="19"><use href="#icon-tested"/></svg>Dermatologist Tested</div>
      <div class="badge"><svg width="19" height="19"><use href="#icon-roots"/></svg>Strengthens Roots</div>
      <div class="badge"><svg width="19" height="19"><use href="#icon-cruelty"/></svg>Cruelty Free</div>
    </div>
    <p class="distributor">Distributed by<br><b>VelaMira</b>,<br>London, UK</p>
  </div>
</section>

<!-- Eyebrow Growth Serum -->
<section class="label label-tube tube-brow">
  <div class="floral-fill" role="img" aria-label="Signature floral pattern of coral watercolour blossoms on pale blue"></div>
  <div class="panel front">
    <div class="brand-slot"><span class="brand-name brand-vertical">VelaMira</span></div>
    <p class="product-name">Eyebrow<br>Growth<br>Serum</p>
    <p class="tagline">Thicker +<br>Fuller Brows</p>
    <p class="volume">5ml/<br>0.17 fl.oz.</p>
  </div>
  <div class="panel back info" style="padding-top:22px">
    <p class="block"><b>Ingredients:</b>Aqua, Biotin, Panthenol, Polysorbate 20</p>
    <p class="block"><b>Caution:</b>For external use only.</p>
    <div class="badges" style="margin-top:20px">
      <div class="badge"><svg width="19" height="19"><use href="#icon-paraben"/></svg>Paraben Free</div>
      <div class="badge"><svg width="19" height="19"><use href="#icon-tested"/></svg>Dermatologist Tested</div>
      <div class="badge"><svg width="19" height="19"><use href="#icon-roots"/></svg>Strengthens Roots</div>
      <div class="badge"><svg width="19" height="19"><use href="#icon-cruelty"/></svg>Cruelty Free</div>
    </div>
    <p class="distributor">Distributed by<br><b>VelaMira</b>,<br>London, UK</p>
  </div>
</section>
</body>
</html>
```